Website for "Bright Morrow Ltd" cleaning bsuiness

We require a website to expose our business to the local market. We want to provide background on who we are and what we do but in an easily digestible way. We clean domestic and commercial premises and want to provide a list of all of our services to potential customers. We operate out of Warrington in the UK.

We would like the website to be animated in some way so that the experience of using it is not dull or mundane. This website needs to be an extension of our company.

Target Market(s)

30 - 60 year olds for Domestic plus commercial clients

Industry/Entity Type

Cleaning Service

Coding

Coded - Design and coding required

Number of Pages Required

4 page

Font styles to use
Sans Serif

Colors
0455a3
3176b5
85acd3
cfdeed
ffffff
000000
1b1b1b
c8c8c8
757575

Requirements
Must have
• Logo which has been provided. Theme based around the logo and its colours. Simple layout to avoid confusion.
Nice to have
• Animations where possible to impress the customer.
Should not have
• any pictures of cleaning equipment, fairies, maids etc

```html
<!DOCTYPE html>
<html lang="en">
<head>
<meta charset="utf-8">
<title>Bright Morrow Ltd – Professional Cleaning Service</title>
<link rel="stylesheet" href="https://fonts.googleapis.com/css2?family=Raleway:wght@300;400;500;600;700&family=Arimo:wght@400;700&family=Playball&display=swap">
<style>
:root{
  --blue:#0455a3;
  --blue-mid:#3176b5;
  --blue-soft:#85acd3;
  --blue-pale:#cfdeed;
  --white:#ffffff;
  --black:#000000;
  --ink:#1b1b1b;
  --line:#c8c8c8;
  --grey:#757575;
}
*{box-sizing:border-box;margin:0;padding:0}
html,body{width:1200px;height:2980px;overflow:hidden;background:var(--white)}
body{font-family:"Arimo",Arial,sans-serif;color:var(--grey)}
.page{position:relative;width:1200px;height:2980px;overflow:hidden}
.abs{position:absolute}
.photo{position:absolute}

/* nav */
.nav{position:absolute;top:0;left:0;width:1200px;height:80px;z-index:5;display:flex;justify-content:center;gap:0}
.nav ul{list-style:none;display:flex;margin-left:-40px}
.nav li{font-family:"Arimo",sans-serif;font-size:17px;color:var(--ink);padding:28px 0 0;height:78px;margin:0 26px}
.nav li.active{color:var(--blue);border-bottom:3px solid var(--blue);padding-left:12px;padding-right:12px}

/* hero */
.hero-photo{left:0;top:0;width:1200px;height:700px;background:linear-gradient(100deg,#dfe3e7 0%,#f4f6f8 35%,#ffffff 55%,#e9eef3 80%,#d6e0ea 100%)}
.brand{position:absolute;top:290px;left:0;width:1200px;text-align:center;font-family:"Raleway",sans-serif;font-weight:600;font-size:76px;color:var(--blue);display:flex;justify-content:center;align-items:center;gap:22px;z-index:3}
.brand .dot{width:30px;height:30px;border-radius:50%;background:var(--blue)}

/* welcome */
.section-title{font-family:"Raleway",sans-serif;font-weight:400;font-size:43px;color:var(--ink);text-align:center;letter-spacing:.5px}
.section-title span{color:var(--blue)}
.welcome-title{top:708px;left:0;width:1200px}
.welcome-text{top:776px;left:140px;width:920px;text-align:center;font-size:13.5px;line-height:27px}
.btn{position:absolute;background:var(--blue);color:var(--white);font-family:"Arimo",sans-serif;font-size:20px;display:flex;align-items:center;justify-content:center}
.know-more{top:922px;left:512px;width:178px;height:58px}

/* service bands */
.band-title{font-family:"Raleway",sans-serif;font-weight:400;font-size:40px;color:var(--white)}
.band-sub{font-family:"Playball",cursive;font-size:19px;color:var(--white)}
.svc-list{list-style:none;color:var(--white);font-size:15px}
.svc-list li{display:flex;align-items:center;height:29px}
.svc-list .mark{width:7px;height:7px;border-radius:50%;background:var(--white);margin:0 22px 0 4px}
.svc-desc{font-size:14px;line-height:26px;color:var(--white)}

/* who / what */
.card-photo{width:228px;height:166px}
.card-title{font-family:"Raleway",sans-serif;font-size:25px;color:var(--ink)}
.card-title span{color:var(--blue)}
.card-text{font-size:13.5px;line-height:26px;width:290px}
.read-more{font-family:"Arimo",sans-serif;font-weight:700;font-size:15px;color:var(--blue);display:flex;align-items:center;gap:4px}

/* testimonial */
.arrow-btn{width:44px;height:44px;border-radius:50%;border:2px solid var(--line);display:flex;align-items:center;justify-content:center}
.quote{top:2436px;left:140px;width:920px;text-align:center;font-size:13.5px;line-height:27px}
.client{top:2506px;left:0;width:1200px;text-align:center;font-family:"Arimo",sans-serif;font-weight:700;font-size:17px;color:var(--blue)}

/* footer */
.footer-bg{left:0;top:2590px;width:1200px;height:350px;background:linear-gradient(90deg,#f7f6f4 0%,#efe7e0 30%,#f6f3f0 55%,#fbfbfb 100%)}
.foot-name{font-family:"Raleway",sans-serif;font-weight:600;font-size:34px;color:var(--blue);line-height:40px}
.foot-head{font-family:"Arimo",sans-serif;font-weight:700;font-size:17px;color:var(--blue);letter-spacing:.4px}
.foot-links{list-style:none;font-size:14px;color:var(--grey)}
.foot-links li{display:flex;align-items:center;height:27px}
.foot-links .sq{width:10px;height:10px;border:1.5px solid var(--blue);margin-right:18px}
.foot-links li:first-child .sq{background:var(--blue)}
.contact-row{display:flex;gap:18px;font-size:14px;line-height:27px;color:var(--grey)}
.news-text{font-size:14px;line-height:26px;color:var(--ink)}
.email-field{top:2816px;left:874px;width:250px;height:40px;border:1px solid var(--line);background:var(--white);font-size:13px;color:var(--ink);padding:12px 10px}
.submit{top:2866px;left:874px;width:156px;height:42px;font-size:18px}
.copyright{left:0;top:2940px;width:1200px;height:40px;background:var(--blue);color:var(--blue-pale);font-size:14px;display:flex;align-items:center;justify-content:center}
.copyright b{color:var(--white);margin:0 4px}
</style>
</head>
<body>
<div class="page">

  <nav class="nav">
    <ul>
      <li class="active">HOME</li>
      <li>ABOUT US</li>
      <li>SERVICES</li>
      <li>BLOG</li>
      <li>CONTACT US</li>
    </ul>
  </nav>

  <!-- hero -->
  <div class="photo hero-photo" role="img" aria-label="Bright, white living room and office interior"></div>
  <div class="brand"><span class="dot"></span>Bright Morrow Ltd</div>
  <svg class="abs" style="left:0;top:560px;z-index:2" width="1200" height="150" viewBox="0 0 1200 150">
    <defs>
      <linearGradient id="heroEdge" x1="0" x2="1">
        <stop offset="0" stop-color="#0455a3"/>
        <stop offset=".55" stop-color="#0455a3"/>
        <stop offset="1" stop-color="#85acd3"/>
      </linearGradient>
    </defs>
    <polygon points="0,122 600,14 1200,122 1200,150 0,150" fill="#ffffff"/>
    <polyline points="0,122 600,14 1200,122" fill="none" stroke="url(#heroEdge)" stroke-width="8"/>
  </svg>

  <!-- welcome -->
  <h1 class="abs section-title welcome-title">WELCOME TO <span>BRIGHT MORROW</span></h1>
  <p class="abs welcome-text">Lorem Ipsum is simply dummy text of the printing and typesetting industry. Lorem Ipsum has been the industry's standard dummy text ever since the 1500s, when an unknown printer took a galley of type and scrambled it to make a type specimen book.It has survived not only five centuries. Lorem Ipsum is simply dummy text of the printing and typesetting industry.<br>Lorem Ipsum is simply dummy text of the printing and typesetting industry. Lorem Ipsum has been the industry's standard dummy text ever since the 1500s, when an unknown printer took a galley of type and scrambled it to make a type specimen book.</p>
  <div class="btn know-more">KNOW MORE</div>

  <!-- domestic -->
  <div class="photo" style="left:560px;top:1040px;width:640px;height:450px;background:linear-gradient(120deg,#b8a995 0%,#d8d0c4 45%,#eeeae4 75%,#c9c2b8 100%)" role="img" aria-label="Folded shirts beside a steam iron on a wooden table"></div>
  <svg class="abs" style="left:0;top:1040px" width="730" height="450" viewBox="0 0 730 450">
    <polygon points="0,0 722,0 472,450 0,450" fill="#0455a3"/>
  </svg>
  <h2 class="abs band-title" style="left:76px;top:1090px">DOMESTIC SERVICES :</h2>
  <p class="abs band-sub" style="left:78px;top:1148px">Weekly, fotnightly, monthly and adhoc cleans available</p>
  <ul class="abs svc-list" style="left:76px;top:1194px">
    <li><span class="mark"></span>Ironing</li>
  </ul>
  <p class="abs svc-desc" style="left:110px;top:1225px">Lorem Ipsum is simply dummy text of the printing and typesetting industry.<br>Lorem Ipsum has been the industry's standard.</p>
  <ul class="abs svc-list" style="left:76px;top:1288px">
    <li><span class="mark"></span>Carpet Cleaning</li>
    <li><span class="mark"></span>Tiled floor steam clean</li>
    <li><span class="mark"></span>End of tenancy clean</li>
    <li><span class="mark"></span>New house pre moving in clean</li>
    <li><span class="mark"></span>Emergency requested clean</li>
  </ul>

  <!-- who / what -->
  <div class="photo card-photo" style="left:78px;top:1557px;background:linear-gradient(135deg,#e9e6e1,#c9b39a 60%,#9b6a3f)" role="img" aria-label="Room with warm wooden floor"></div>
  <h3 class="abs card-title" style="left:322px;top:1550px">Who We <span>Are ?</span></h3>
  <p class="abs card-text" style="left:326px;top:1590px">Lorem Ipsum is simply dummy text of the printing and typesetting industry. Lorem Ipsum has been the industry's standard dummy text ever since the.</p>
  <div class="abs read-more" style="left:326px;top:1704px">READ MORE...
    <svg width="14" height="12" viewBox="0 0 14 12"><path d="M1 1l5 5-5 5M7 1l5 5-5 5" fill="none" stroke="#0455a3" stroke-width="2"/></svg></div>

  <div class="photo card-photo" style="left:612px;top:1557px;background:linear-gradient(135deg,#f3f3f1,#e2e3df 55%,#cfd3cc)" role="img" aria-label="Bright living room with sofa"></div>
  <h3 class="abs card-title" style="left:856px;top:1550px">What We <span>Do ?</span></h3>
  <p class="abs card-text" style="left:860px;top:1590px">Lorem Ipsum is simply dummy text of the printing and typesetting industry. Lorem Ipsum has been the industry's standard dummy text ever since the.</p>
  <div class="abs read-more" style="left:860px;top:1704px">READ MORE...
    <svg width="14" height="12" viewBox="0 0 14 12"><path d="M1 1l5 5-5 5M7 1l5 5-5 5" fill="none" stroke="#0455a3" stroke-width="2"/></svg></div>

  <!-- commercial -->
  <div class="photo" style="left:0;top:1786px;width:760px;height:396px;background:linear-gradient(135deg,#a89c88 0%,#d9cfbf 40%,#c6b9a5 70%,#8f826f 100%)" role="img" aria-label="Tiled floor being cleaned"></div>
  <svg class="abs" style="left:480px;top:1786px" width="720" height="396" viewBox="0 0 720 396">
    <polygon points="10,0 720,0 720,396 240,396" fill="#0455a3"/>
  </svg>
  <h2 class="abs band-title" style="right:76px;top:1838px">COMMERCIAL CLEANING</h2>
  <p class="abs band-sub" style="right:78px;top:1896px">contract daily cleaning</p>
  <ul class="abs svc-list" style="right:74px;top:1942px;text-align:right">
    <li style="justify-content:flex-end;font-size:18px">Vacuuming<span class="mark" style="margin:0 4px 0 14px"></span></li>
  </ul>
  <p class="abs svc-desc" style="right:78px;top:1976px;text-align:right">Lorem Ipsum is simply dummy text of the printing and typesetting industry.<br>Lorem Ipsum has been the industry's standard.</p>
  <ul class="abs svc-list" style="right:74px;top:2036px">
    <li style="justify-content:flex-end">Desk polishing<span class="mark" style="margin:0 4px 0 20px"></span></li>
    <li style="justify-content:flex-end">Bin emptying<span class="mark" style="margin:0 4px 0 20px"></span></li>
    <li style="justify-content:flex-end">Toilet cleaning<span class="mark" style="margin:0 4px 0 20px"></span></li>
  </ul>

  <!-- testimonial -->
  <h2 class="abs section-title" style="left:0;top:2238px;width:1200px">WHAT OUR <span>CLIENT SAY</span></h2>
  <div class="abs" style="left:546px;top:2312px;width:110px;height:110px;border-radius:50%;border:3px solid var(--line);background:linear-gradient(135deg,#f1e3d3,#d8b998)" role="img" aria-label="Client portrait"></div>
  <div class="abs arrow-btn" style="left:76px;top:2350px"><svg width="14" height="14" viewBox="0 0 14 14"><path d="M9 2L4 7l5 5" fill="none" stroke="#c8c8c8" stroke-width="2"/></svg></div>
  <div class="abs arrow-btn" style="left:1080px;top:2350px"><svg width="14" height="14" viewBox="0 0 14 14"><path d="M5 2l5 5-5 5" fill="none" stroke="#c8c8c8" stroke-width="2"/></svg></div>
  <p class="abs quote">Lorem Ipsum is simply dummy text of the printing and typesetting industry. Lorem Ipsum has been the industry's standard dummy text ever since the 1500s, when an unknown printer took a galley&nbsp; tmake a type specimen book.</p>
  <p class="abs client">- CLIENT NAME</p>

  <!-- footer -->
  <div class="photo footer-bg" role="img" aria-label="Soft, faded photo of a smiling woman on a clean carpet"></div>
  <svg class="abs" style="left:0;top:2580px" width="1200" height="120" viewBox="0 0 1200 120">
    <polygon points="0,0 1200,0 1200,110 600,12 0,110" fill="#ffffff"/>
    <polyline points="0,110 600,12 1200,110" fill="none" stroke="#0455a3" stroke-width="7"/>
  </svg>

  <div class="abs" style="left:84px;top:2740px;display:flex;align-items:center;gap:12px">
    <span style="width:18px;height:18px;border-radius:50%;background:var(--blue)"></span>
    <p class="foot-name">Bright Morrow<br>Ltd</p>
  </div>

  <h4 class="abs foot-head" style="left:352px;top:2702px">USEFULL LINKS</h4>
  <ul class="abs foot-links" style="left:352px;top:2738px">
    <li><span class="sq"></span>Home</li>
    <li><span class="sq"></span>About Us</li>
    <li><span class="sq"></span>Services</li>
    <li><span class="sq"></span>Blog</li>
    <li><span class="sq"></span>Contact Us</li>
  </ul>

  <h4 class="abs foot-head" style="left:608px;top:2702px">GET IN TOUCH</h4>
  <div class="abs contact-row" style="left:608px;top:2740px">
    <svg width="20" height="20" viewBox="0 0 20 20" style="margin-top:4px"><path d="M1 4l6-2 6 2 6-2v14l-6 2-6-2-6 2z M7 2v14 M13 4v14" fill="none" stroke="#0455a3" stroke-width="1.5"/></svg>
    <span style="width:200px">101- Lorem ipsum is simple dummy text of print and type setting industry</span>
  </div>
  <div class="abs contact-row" style="left:608px;top:2830px">
    <svg width="20" height="20" viewBox="0 0 20 20" style="margin-top:4px"><path d="M4 2l3 0 2 5-2 2c1 2 3 4 5 5l2-2 5 2v3c0 1-1 2-2 2C9 19 1 11 2 4c0-1 1-2 2-2z" fill="none" stroke="#0455a3" stroke-width="1.5"/></svg>
    <span>123 456 7890</span>
  </div>
  <div class="abs contact-row" style="left:608px;top:2874px">
    <svg width="20" height="20" viewBox="0 0 20 20" style="margin-top:4px"><rect x="1.5" y="4" width="17" height="12" fill="none" stroke="#0455a3" stroke-width="1.5"/><path d="M1.5 4l8.5 7 8.5-7" fill="none" stroke="#0455a3" stroke-width="1.5"/></svg>
    <span>hello@brightmorrow.co.uk</span>
  </div>

  <h4 class="abs foot-head" style="left:876px;top:2702px">NEWSLETTER</h4>
  <p class="abs news-text" style="left:876px;top:2736px;width:260px">Would you like to receive exclusive access to articles, white papers and our regular monthly newsletter?</p>
  <div class="abs email-field">Enter Email Id</div>
  <div class="btn submit">SUBMIT</div>

  <div class="abs copyright">© 2016 <b>Bright Morrow</b> - &nbsp;All rights reserved.</div>
</div>
</body>
</html>
```